Re-style home page - eye-catching and unique design for social commerce website

We need a new concept design for BrinoKet's home page.
We don't want to make huge changes but creating a more professional and eye-catching style.

We need to look very serious like a professional services company and in the same time to look like a social network for e-commerce.

Our logo is very captive and you can use to creating something of harmonious.

This is a re-style and I'm excepted to see unique and fresh design like Glimmora.

Target Market(s)

e-commerce and social

Industry/Entity Type

Social

Number of Pages Required

1 page

Font styles to use
Serif
Sans Serif

Requirements
Must have
• An eye-catching result.
• Search bar with logo and Login How it works and business
• The slogan with login and signup.
• Footer links.
Nice to have
• I would like to open the home page and see only two clear ways:
• -Consumer
• --Search
• --The slogan
• --Login and Signup
• --How it works
• -Business
• --Go to Business area
• Background: City, Shopping.
Should not have
• Scrollbar style!

```html
<!DOCTYPE html>
<html lang="en">
<head>
<meta charset="utf-8">
<title>BrinoKet — Shop directly from your profile</title>
<link href="https://fonts.googleapis.com/css2?family=Roboto:wght@300;400;500;700&family=Great+Vibes&display=swap" rel="stylesheet">
<style>
  :root {
    --header-bg: #222224;
    --footer-bg: #2b2a2c;
    --white: #ffffff;
    --text-muted: #d8d8d8;
    --search-pink: #ea356b;
    --signup-orange: #ee7f1e;
    --signup-orange-dark: #e36f12;
    --social-blue: #3e5b9a;
    --social-blue-dark: #344e86;
    --field-border: #d6d6d6;
    --placeholder: #8a8a8a;
    --circle-a: #3b5b98;
    --circle-b: #2aa2df;
    --circle-c: #444446;
    --circle-d: #c9252d;
    --circle-e: #dc4a2e;
    --circle-f: #d9302b;
  }
  * { box-sizing: border-box; margin: 0; padding: 0; }
  html, body { width: 1200px; height: 693px; overflow: hidden; background: var(--header-bg); }
  body { font-family: "Roboto", Arial, sans-serif; color: var(--white); position: relative; }

  .site-header {
    position: absolute; left: 0; top: 0; width: 1200px; height: 83px;
    background: var(--header-bg);
  }
  .brand {
    position: absolute; left: 76px; top: 24px;
    font-size: 32px; font-weight: 700; letter-spacing: -0.5px; color: var(--white);
    display: flex; align-items: center; gap: 8px;
  }
  .brand-dot { width: 14px; height: 14px; background: var(--signup-orange); border-radius: 50%; }
  .search-bar { position: absolute; left: 343px; top: 19px; width: 515px; height: 45px; display: flex; }
  .search-input {
    flex: 1; border: 0; background: var(--white); padding: 0 14px;
    font: italic 300 15px "Roboto", Arial, sans-serif; color: var(--placeholder);
    display: flex; align-items: center; border-radius: 2px 0 0 2px;
  }
  .search-button {
    width: 88px; background: var(--search-pink); color: var(--white);
    font-size: 14px; font-weight: 500; letter-spacing: 0.5px;
    display: flex; align-items: center; justify-content: center; border-radius: 0 2px 2px 0;
  }
  .main-nav {
    position: absolute; right: 72px; top: 35px;
    display: flex; gap: 12px; font-size: 10.5px; font-weight: 500; letter-spacing: 0.3px;
  }
  .main-nav .sep { color: var(--text-muted); }

  .hero {
    position: absolute; left: 0; top: 83px; width: 1200px; height: 493px;
    background: radial-gradient(circle at 12% 35%, #9a8a72 0%, transparent 35%),
                radial-gradient(circle at 90% 30%, #c79a48 0%, transparent 30%),
                radial-gradient(circle at 85% 80%, #b7862f 0%, transparent 28%),
                linear-gradient(100deg, #6b6258 0%, #8b7a66 40%, #7a6e61 70%, #8f7448 100%);
  }
  .signup-card {
    position: absolute; left: 206px; top: 32px; width: 788px; height: 426px;
    border: 3px solid rgba(255,255,255,0.8);
    box-shadow: 0 0 10px rgba(0,0,0,0.3);
    background: linear-gradient(100deg, #8e7d66 0%, #b59d7c 35%, #a57f5a 60%, #8b6a4c 100%);
    text-align: center;
  }
  .card-brand {
    position: absolute; left: 0; right: 0; top: 36px;
    font-size: 25px; font-weight: 700; display: flex; justify-content: center; align-items: center; gap: 6px;
  }
  .card-brand .brand-dot { width: 11px; height: 11px; }
  .tagline {
    position: absolute; left: 0; right: 0; top: 78px;
    font-family: "Great Vibes", cursive; font-size: 46px; font-weight: 400;
  }
  .subline { position: absolute; left: 0; right: 0; top: 146px; font-size: 20px; font-weight: 400; }
  .social-login {
    position: absolute; left: 296px; top: 178px; width: 192px; height: 37px;
    background: var(--social-blue); border: 1px solid var(--social-blue-dark); border-radius: 3px;
    display: flex; align-items: center; font-size: 12.5px; font-weight: 500;
  }
  .social-login .mark { width: 37px; height: 100%; border-right: 1px solid var(--social-blue-dark); }
  .social-login span { flex: 1; }
  .divider {
    position: absolute; left: 226px; top: 244px; width: 336px;
    display: flex; align-items: center; gap: 8px; font-size: 13px; font-weight: 300;
  }
  .divider::before, .divider::after { content: ""; flex: 1; height: 1px; background: rgba(255,255,255,0.55); }
  .field {
    position: absolute; top: 270px; width: 242px; height: 39px;
    background: var(--white); border: 1px solid var(--field-border);
    color: var(--placeholder); font-size: 13px; text-align: left; padding: 12px 15px 0;
  }
  .field-email { left: 142px; }
  .field-password { left: 398px; }
  .signup-button {
    position: absolute; left: 315px; top: 328px; width: 153px; height: 42px;
    background: linear-gradient(var(--signup-orange), var(--signup-orange-dark));
    border-radius: 2px; font-size: 15px; font-weight: 500; letter-spacing: 0.5px;
    display: flex; align-items: center; justify-content: center;
  }
  .terms { position: absolute; left: 0; right: 0; top: 389px; font-size: 11px; font-weight: 300; }

  .site-footer { position: absolute; left: 0; top: 576px; width: 1200px; height: 117px; background: var(--footer-bg); }
  .footer-links {
    position: absolute; left: 75px; top: 37px; display: flex; gap: 16px;
    font-size: 14.5px; font-weight: 300;
  }
  .footer-links .sep { color: var(--text-muted); }
  .copyright { position: absolute; left: 75px; top: 65px; font-size: 10.5px; font-weight: 300; color: var(--text-muted); }
  .social-list { position: absolute; left: 917px; top: 44px; display: flex; gap: 5px; }
  .social-list li { list-style: none; width: 31px; height: 31px; border-radius: 50%; }
</style>
</head>
<body>
  <header class="site-header">
    <div class="brand"><span>BrinoKet</span><span class="brand-dot"></span></div>
    <div class="search-bar">
      <div class="search-input">Search Keywords</div>
      <div class="search-button">SEARCH</div>
    </div>
    <nav class="main-nav">
      <span>LOGIN</span><span class="sep">|</span>
      <span>HOW IT WORKS</span><span class="sep">|</span>
      <span>BUSINESS</span>
    </nav>
  </header>

  <section class="hero" role="img" aria-label="Blurred city shopping street with warm bokeh lights">
    <div class="signup-card" role="img" aria-label="Photo of a smiling shopper holding bags and a phone in a cafe">
      <div class="card-brand"><span>BrinoKet</span><span class="brand-dot"></span></div>
      <h1 class="tagline">Shop directly from your profile</h1>
      <p class="subline">Save your time. Live better.</p>
      <div class="social-login"><div class="mark"></div><span>Login with Connectly</span></div>
      <div class="divider">Or</div>
      <div class="field field-email">Enter Email</div>
      <div class="field field-password">Create a &nbsp;Password</div>
      <div class="signup-button">SIGN UP</div>
      <p class="terms">Creating an account means you're okay with BrinoKet Terms of Service and Privacy Policy.</p>
    </div>
  </section>

  <footer class="site-footer">
    <nav class="footer-links">
      <span>About us</span><span class="sep">/</span>
      <span>Blog</span><span class="sep">/</span>
      <span>Business</span><span class="sep">/</span>
      <span>Jobs</span><span class="sep">/</span>
      <span>Privacy</span><span class="sep">/</span>
      <span>FAQ</span><span class="sep">/</span>
      <span>Contacts</span>
    </nav>
    <p class="copyright">Copyright ©2015.Company Name.All Right Reserved</p>
    <ul class="social-list">
      <li style="background:var(--circle-a)" aria-label="Connectly"></li>
      <li style="background:var(--circle-b)" aria-label="Chirpline"></li>
      <li style="background:var(--circle-c)" aria-label="Snapframe"></li>
      <li style="background:var(--circle-d)" aria-label="Glimmora"></li>
      <li style="background:var(--circle-e)" aria-label="Circlenet"></li>
      <li style="background:var(--circle-f)" aria-label="Reelcast"></li>
    </ul>
  </footer>
</body>
</html>
```